BUSINESS CARD - HALLORAN FIELD SERVICES

I would like to create a business card for my fertilizer spreading business. I would like to incorporate my existing logo and also a description of the services offered. The business card will be given to farmers so must be kept simple but effective. It will also be left in stores so much also be eye catching in order to stand out from other cards.

Target Market(s)

FARMERS

Requirements
Must have
• FRONT OF CARD = EXISTING LOGO + "CUSTOMISED SPREADING" below the logo

REAR Of CARD = SERVICES OFFERED AND CONTACT DETAILS

- Bulk fertilizer including Lime, Gypsum, Manure & Compost
- Granular fertilizer including Single Super, Urea, Gran-am, & Custom Blends
- Modern equipment - Autosteer & Variable Rate Capable
- Friendly & Reliable Service
- Contact Gus: 0417 552 308
Nice to have
• utilize same color scheme as existing logo

```html
<!DOCTYPE html>
<html lang="en">
<head>
<meta charset="utf-8">
<title>Halloran Field Services – Business Card</title>
<link rel="stylesheet" href="https://fonts.googleapis.com/css2?family=Arimo:wght@400;700&display=swap">
<style>
  :root {
    --backdrop: #262626;
    --card-white: #ffffff;
    --card-grey: #59595b;
    --ink-grey: #58585a;
    --accent-orange: #f7941d;
    --text-light: #ffffff;
    --rule-soft: rgba(255, 255, 255, 0.35);
  }
  * { box-sizing: border-box; margin: 0; padding: 0; }
  html, body {
    width: 1200px;
    height: 900px;
    overflow: hidden;
    background: var(--backdrop);
    font-family: "Arimo", Arial, sans-serif;
  }
  .sheet {
    width: 1200px;
    height: 900px;
    display: flex;
    flex-direction: column;
    align-items: center;
    justify-content: center;
    gap: 40px;
  }
  .card {
    width: 560px;
    height: 320px;
    display: flex;
    flex-direction: column;
    align-items: center;
    justify-content: center;
    text-align: center;
  }
  .card--front { background: var(--card-white); }
  .card--back { background: var(--card-grey); }

  .brand {
    display: flex;
    align-items: center;
    gap: 14px;
  }
  .brand__mark {
    width: 54px;
    height: 54px;
    flex: none;
  }
  .brand__name {
    color: var(--ink-grey);
    font-weight: 700;
    font-size: 28px;
    letter-spacing: 0.5px;
  }
  .brand__rule {
    width: 380px;
    height: 2px;
    background: var(--accent-orange);
    margin-top: 14px;
  }
  .tagline {
    margin-top: 16px;
    color: var(--accent-orange);
    font-size: 19px;
    letter-spacing: 3px;
  }

  .services {
    list-style: none;
    color: var(--text-light);
    font-size: 16px;
    line-height: 1.45;
  }
  .divider {
    width: 340px;
    height: 1px;
    background: var(--rule-soft);
    margin: 16px 0 14px;
  }
  .contact {
    color: var(--accent-orange);
    font-size: 28px;
  }
</style>
</head>
<body>
<main class="sheet">
  <section class="card card--front" aria-label="Card front">
    <div class="brand">
      <svg class="brand__mark" viewBox="0 0 54 54" aria-hidden="true">
        <circle cx="27" cy="27" r="24" fill="none" stroke="#58585a" stroke-width="4"/>
      </svg>
      <span class="brand__name">HALLORAN FIELD SERVICES</span>
    </div>
    <div class="brand__rule"></div>
    <p class="tagline">CUSTOMISED SPREADING</p>
  </section>

  <section class="card card--back" aria-label="Card back">
    <ul class="services">
      <li>Bulk fertilizer including Lime, Gypsum, Manure &amp; Compost</li>
      <li>Granular fertilizer including Single Super, Urea</li>
      <li>Gran-am, &amp; Custom Blends</li>
      <li>Modern equipment</li>
      <li>Autosteer &amp; Variable Rate Capable</li>
      <li>Friendly &amp; Reliable Service</li>
    </ul>
    <div class="divider"></div>
    <p class="contact">Contact Gus: 0417 552 308</p>
  </section>
</main>
</body>
</html>
```